Financial & Tax Strategies

need to get a word press site with existing domains and condense existing content on existing site, make new site dynamic, need mobile too......need to take info from my quorvia website and get modern, relevant site, less verbose on first page, way more things to click and engage people. Would like it to look like this , but with my color scheme and not quite as busy looking. I like much of the content on my tabs. Want maximize by seo capabilities on their as well. The number one thing I can say is to go to my existing website and get content, logo, etc there … www.pinegatelarkgroup.com .

Target Market(s)

Those 40 -65, business owners for at least 5 years. Higher net worth.

Number of Pages Required

5+ page

Font styles to use
Sans Serif

Colors
f04a50
e4daeb
ffffff

Requirements
Must have
• seo maximized, lots of places to click on to contact us, calls to action, relevant, conservative, want it to look like this and have the function as well.....slight variation on messaging, but like the simplicity on first view. https://www.dorrickvale.com/
Nice to have
• Some area along right side where videos we do will be.
Should not have
• feel too busy, but still have lots of opportunities to engage.

```html
<!DOCTYPE html>
<html lang="en">
<head>
<meta charset="utf-8">
<title>Pinegate Lark Group – Financial &amp; Tax Strategies</title>
<link href="https://fonts.googleapis.com/css2?family=Lato:wght@400;700&family=Roboto:wght@400;500&display=swap" rel="stylesheet">
<style>
:root{
  --red:#e8202a;
  --ink:#222222;
  --text:#555555;
  --muted:#8a8a8a;
  --light:#f3f3f3;
  --band:#ececec;
  --white:#ffffff;
  --footer:#2b2b2b;
  --line:#e2e2e2;
  --blue:#2f6fb0;
}
*{box-sizing:border-box;margin:0;padding:0}
html,body{width:1200px;height:3636px;overflow:hidden}
body{position:relative;background:var(--white);font-family:"Roboto",Arial,sans-serif;color:var(--text)}
.abs{position:absolute}
h2.section-title{position:absolute;left:0;width:1200px;text-align:center;font-family:"Lato",Arial,sans-serif;font-weight:400;font-size:34px;color:var(--ink)}
.btn{position:absolute;background:var(--red);color:var(--white);border-radius:20px;font-size:13px;font-weight:500;display:flex;align-items:center;justify-content:center}

/* header */
.site-header{top:0;left:0;width:1200px;height:102px;background:var(--white)}
.menu-icon{left:80px;top:36px;width:24px}
.menu-icon span{display:block;height:2px;background:#333;margin-bottom:5px}
.brand{left:492px;top:26px;display:flex;align-items:center;gap:12px}
.brand-mark{width:44px;height:44px;border-radius:50%;background:#555}
.brand-name{font-family:"Lato",Arial,sans-serif;font-size:21px;line-height:24px;color:#333}
.call{left:990px;top:32px;display:flex;gap:10px;align-items:center}
.call-icon{width:28px;height:28px;border-radius:50%;background:var(--red)}
.call-text{font-size:13px;line-height:16px;color:var(--red)}
.call-text b{display:block;color:#333;font-weight:400}

/* hero */
.hero{top:102px;left:0;width:1200px;height:536px;background:linear-gradient(180deg,#6e9a4a 0%,#4f8a36 35%,#79a845 62%,#3f6a3a 80%,#556f4c 100%)}
.hero-box{left:346px;top:196px;width:510px;height:180px;border:1px solid rgba(255,255,255,.6);background:rgba(255,255,255,.12);text-align:center;color:var(--white)}
.hero-box h1{font-family:"Lato",Arial,sans-serif;font-weight:400;font-size:38px;margin-top:30px}
.hero-box p{font-size:13px;line-height:16px;margin:8px auto 0;width:380px}
.hero .btn{left:519px;top:337px;width:162px;height:38px}
.arrow{top:250px}
.dots{top:498px;left:578px;display:flex;gap:8px}
.dots i{width:7px;height:7px;border-radius:50%;background:rgba(255,255,255,.6)}
.dots i.on{background:var(--white)}

/* about */
.divider{top:752px;left:545px;width:110px;height:20px}
.about-text{top:793px;left:225px;width:750px;text-align:center;font-size:13px;line-height:16px;color:#444}

/* services */
.subtitle{position:absolute;left:0;width:1200px;text-align:center;font-size:12px;color:var(--muted)}
.service{top:1071px;width:243px;height:274px;background:var(--white);border-radius:14px;box-shadow:0 2px 10px rgba(0,0,0,.06);text-align:center;padding-top:26px}
.service svg.ico{width:48px;height:48px}
.service h3{font-family:"Lato",Arial,sans-serif;font-weight:400;font-size:18px;line-height:22px;color:#333;margin:14px 20px 16px}
.service p{font-size:13px;line-height:16px;color:var(--muted);margin:0 26px}
.service .go{position:absolute;left:111px;bottom:20px}
.service.active{background:var(--red)}
.service.active h3,.service.active p{color:var(--white)}
.services-bg{top:940px;left:0;width:1200px;height:505px;background:var(--light)}

/* graphs */
.graph-band{top:1445px;left:0;width:1200px;height:514px;background:linear-gradient(135deg,#e4e4e4,#f1f1f1 50%,#e6e6e6)}
.graph-title{left:80px;top:1538px;width:470px;font-family:"Lato",Arial,sans-serif;font-weight:400;font-size:32px;line-height:40px;color:#333}
.graph-copy{left:80px;top:1658px;width:455px;font-size:13px;line-height:16px;color:#666}
.graph-copy p{margin-bottom:10px}
.chart-panel{left:560px;top:1520px;width:600px;height:360px;background:var(--white);border:10px solid #2e2e2e;border-radius:8px}

/* blogs */
.blog{top:2094px;width:345px;height:391px;background:var(--white);box-shadow:0 2px 10px rgba(0,0,0,.08)}
.blog-photo{margin:14px 14px 0;height:210px}
.blog-meta{display:flex;justify-content:space-between;margin:12px 14px 0;font-size:12px;color:#555}
.blog-meta span{display:flex;align-items:center;gap:6px}
.blog h4{margin:26px 14px 6px;font-size:13px;font-weight:500;color:#333}
.blog p{margin:0 14px;font-size:13px;line-height:16px;color:#444}
.blog .more{display:inline-block;margin:10px 14px 0;font-size:12px;color:#333;border-bottom:1px solid #333}

/* testimonials */
.testimonial-bg{top:2570px;left:0;width:1200px;height:480px;background:var(--light)}
.testimonial{top:2669px;width:300px;height:301px;background:var(--white);border-radius:16px;text-align:center;padding-top:30px}
.avatar{width:104px;height:104px;border-radius:50%;margin:0 auto;background:linear-gradient(160deg,#c9cbd0,#7c818a)}
.testimonial h5{font-size:16px;font-weight:400;color:#333;margin-top:16px}
.testimonial .role{font-size:13px;color:var(--red);margin-top:3px}
.testimonial p{font-size:13px;line-height:16px;color:#444;margin:10px 40px 0}
.testimonial .go{position:absolute;left:141px;bottom:22px}
.t-dots{top:3004px;left:582px;display:flex;gap:7px}
.t-dots i{width:7px;height:7px;border-radius:50%;background:#999}
.t-dots i.on{background:var(--red)}

/* newsletter */
.newsletter-bg{top:3050px;left:0;width:1200px;height:208px;background:var(--light)}
.news-input{left:318px;top:3166px;width:420px;height:36px;background:var(--white);border-radius:18px;font-size:12px;color:#999;padding:11px 26px}
.news-btn{left:746px;top:3166px;width:165px;height:36px}

/* footer */
.site-footer{top:3258px;left:0;width:1200px;height:325px;background:var(--footer);color:#ddd}
.f-brand{left:80px;top:50px;display:flex;align-items:center;gap:12px}
.f-brand .brand-mark{background:#eee;width:46px;height:46px}
.f-brand .brand-name{color:var(--white)}
.f-about{left:80px;top:118px;width:260px;font-size:13px;line-height:16px}
.f-read{left:80px;top:226px;font-size:13px;border-bottom:1px solid #ddd}
.f-head{font-size:15px;color:var(--white);border-bottom:2px solid var(--red);padding-bottom:6px;display:inline-block}
.f-links{left:415px;top:56px}
.f-links ul{list-style:none;margin-top:14px}
.f-links li{font-size:13px;line-height:22px}
.f-links li::before{content:"•";margin-right:10px}
.f-address{left:587px;top:56px;width:200px}
.f-address .row{display:flex;gap:12px;font-size:13px;line-height:16px;margin-top:10px}
.f-address .row:first-of-type{margin-top:18px}
.f-address svg{flex:none;margin-top:1px}
.f-contact{left:827px;top:56px;width:292px}
.f-fields{display:flex;gap:4px;margin-top:14px}
.f-fields span{flex:1;height:26px;background:#4a4a4a;font-size:11px;color:#ddd;padding:7px 8px}
.f-message{height:70px;background:#4a4a4a;margin-top:6px}
.f-btn{position:relative;display:flex;align-items:center;justify-content:center;width:140px;height:32px;background:var(--red);color:var(--white);border-radius:16px;font-size:13px;margin-top:8px}
.bottom-bar{top:3583px;left:0;width:1200px;height:53px;background:var(--white)}
.copy{left:80px;top:20px;font-size:12px;color:#333}
.socials{left:935px;top:14px;display:flex;gap:12px}
.socials i{width:24px;height:24px;border-radius:50%;background:var(--red)}
.socials i:nth-child(n+2){background:#222}
</style>
</head>
<body>

<header class="site-header abs">
  <div class="menu-icon abs"><span></span><span></span><span></span></div>
  <div class="brand abs"><span class="brand-mark"></span><span class="brand-name">Pinegate Lark<br>Group</span></div>
  <div class="call abs">
    <span class="call-icon"></span>
    <div class="call-text">Call us Now<b>555.014.2277</b></div>
  </div>
</header>

<section class="hero abs" role="img" aria-label="Green valley with farmhouses beside a lake">
  <svg class="arrow abs" style="left:40px" width="20" height="30" viewBox="0 0 20 30"><path d="M16 2 4 15l12 13" fill="none" stroke="#fff" stroke-width="4"/></svg>
  <svg class="arrow abs" style="left:1142px" width="20" height="30" viewBox="0 0 20 30"><path d="M4 2l12 13L4 28" fill="none" stroke="#fff" stroke-width="4"/></svg>
  <div class="hero-box abs">
    <h1>Financial &amp; Tax Strategies</h1>
    <p>Lorem Ipsum is a simply dummy text of the printing and industry when an unknown printer took galley of type.</p>
  </div>
  <div class="btn" style="left:519px;top:337px;width:162px;height:38px">Get A Quote</div>
  <div class="dots abs"><i></i><i class="on"></i><i></i><i></i></div>
</section>

<h2 class="section-title" style="top:706px">About us</h2>
<svg class="divider abs" viewBox="0 0 110 20"><line x1="0" y1="10" x2="38" y2="10" stroke="#e8202a" stroke-width="2"/><circle cx="55" cy="10" r="7" fill="none" stroke="#666" stroke-width="3"/><line x1="72" y1="10" x2="110" y2="10" stroke="#e8202a" stroke-width="2"/></svg>
<p class="about-text abs">When the market is up, all advisors are brilliant. It's when the market corrects or crashes, and it always does, that all those gains are erased. How many years did it take to go up, then fall and how long to come back from the years of this process? Avoiding these "corrections" is one key.</p>
<div class="btn" style="left:517px;top:866px;width:166px;height:38px">Read More</div>

<div class="services-bg abs"></div>
<h2 class="section-title" style="top:962px">We Provide Best Services</h2>
<p class="subtitle" style="top:1008px">Lorem Ipsum is simply dummy text of the printing</p>

<article class="service abs" style="left:80px">
  <svg class="ico" viewBox="0 0 48 48"><rect x="8" y="26" width="6" height="14" fill="#e8202a"/><rect x="18" y="20" width="6" height="20" fill="#e8202a"/><rect x="28" y="24" width="6" height="16" fill="#e8202a"/><rect x="38" y="16" width="6" height="24" fill="#e8202a"/><path d="M8 18 20 10l10 6 12-10" fill="none" stroke="#e8202a" stroke-width="2"/></svg>
  <h3>Market Crash<br>Protection</h3>
  <p>Lorem Ipsum is a simply dummy text of the printing and industry when an unknown printer took galley of type.</p>
  <svg class="go" width="20" height="20" viewBox="0 0 20 20"><circle cx="10" cy="10" r="8" fill="none" stroke="#333" stroke-width="1.6"/><path d="M6 10h8M10 6l4 4-4 4" fill="none" stroke="#333" stroke-width="1.6"/></svg>
</article>
<article class="service active abs" style="left:347px">
  <svg class="ico" viewBox="0 0 48 48"><path d="M14 8v22h22M14 20h16l4-10" fill="none" stroke="#fff" stroke-width="3"/><path d="M6 38c10 6 26 6 38-4" fill="none" stroke="#fff" stroke-width="3"/></svg>
  <h3>Fees Kill Retirement<br>Planning</h3>
  <p>Lorem Ipsum is a simply dummy text of the printing and industry when an unknown printer took galley of type.</p>
  <svg class="go" width="20" height="20" viewBox="0 0 20 20"><circle cx="10" cy="10" r="8" fill="none" stroke="#fff" stroke-width="1.6"/><path d="M6 10h8M10 6l4 4-4 4" fill="none" stroke="#fff" stroke-width="1.6"/></svg>
</article>
<article class="service abs" style="left:611px">
  <svg class="ico" viewBox="0 0 48 48"><rect x="8" y="8" width="32" height="34" fill="none" stroke="#e8202a" stroke-width="3"/><rect x="12" y="12" width="24" height="10" fill="#e8202a"/><path d="M14 28h20M14 34h20" stroke="#e8202a" stroke-width="2"/></svg>
  <h3>Tax<br>Avoidance</h3>
  <p>Lorem Ipsum is a simply dummy text of the printing and industry when an unknown printer took galley of type.</p>
  <svg class="go" width="20" height="20" viewBox="0 0 20 20"><circle cx="10" cy="10" r="8" fill="none" stroke="#333" stroke-width="1.6"/><path d="M6 10h8M10 6l4 4-4 4" fill="none" stroke="#333" stroke-width="1.6"/></svg>
</article>
<article class="service abs" style="left:877px">
  <svg class="ico" viewBox="0 0 48 48"><circle cx="24" cy="14" r="9" fill="#e8202a"/><path d="M24 23v11M16 34h16l-3 10H19z" fill="#e8202a" stroke="#e8202a" stroke-width="2"/></svg>
  <h3>Baby Boomer<br>Wealth Building</h3>
  <p>Lorem Ipsum is a simply dummy text of the printing and industry when an unknown printer took galley of type.</p>
  <svg class="go" width="20" height="20" viewBox="0 0 20 20"><circle cx="10" cy="10" r="8" fill="none" stroke="#333" stroke-width="1.6"/><path d="M6 10h8M10 6l4 4-4 4" fill="none" stroke="#333" stroke-width="1.6"/></svg>
</article>

<section class="graph-band abs"></section>
<h2 class="graph-title abs">Graphs can speak a thousand words</h2>
<div class="graph-copy abs">
  <p>Graphs can speak a thousand words. Here's one people really see value in. It basically shows how a $100,000.00 investment in a so-called "diversified" portfolio mirroring the Market Index would have performed between 2000 &amp; 2010 and how one of our products would have performed.</p>
  <p>Harlan Mercer's number one rule is demonstrated here.......DON'T LOSE MONEY. Again, we deconstruct what has been made to be difficult back to simple. Yes....</p>
</div>
<div class="btn" style="left:80px;top:1823px;width:166px;height:38px">Read More</div>

<div class="chart-panel abs">
  <svg width="580" height="340" viewBox="0 0 580 340" font-family="Roboto,Arial,sans-serif">
    <text x="290" y="16" text-anchor="middle" font-size="11" font-weight="700" fill="#222">Ten-Year Comparison: Market Index vs. Floor and Cap Strategy</text>
    <text x="290" y="30" text-anchor="middle" font-size="10" fill="#222">Growth with a 0% floor and 13% cap on annual returns</text>
    <g stroke="#ddd" stroke-width="1">
      <line x1="50" y1="50" x2="560" y2="50"/><line x1="50" y1="86" x2="560" y2="86"/><line x1="50" y1="122" x2="560" y2="122"/><line x1="50" y1="158" x2="560" y2="158"/><line x1="50" y1="194" x2="560" y2="194"/><line x1="50" y1="230" x2="560" y2="230"/><line x1="50" y1="266" x2="560" y2="266"/>
    </g>
    <g font-size="10" fill="#333" text-anchor="end">
      <text x="44" y="54">120.00%</text><text x="44" y="90">80.00%</text><text x="44" y="126">40.00%</text><text x="44" y="162">0%</text><text x="44" y="198">-40.00%</text><text x="44" y="234">-80.00%</text><text x="44" y="270">-120.00%</text>
    </g>
    <g font-size="10" fill="#333" text-anchor="middle">
      <text x="68" y="288">00</text><text x="113" y="288">01</text><text x="158" y="288">02</text><text x="203" y="288">03</text><text x="248" y="288">04</text><text x="293" y="288">05</text><text x="338" y="288">06</text><text x="383" y="288">07</text><text x="428" y="288">08</text><text x="473" y="288">09</text><text x="518" y="288">10</text>
    </g>
    <polyline points="68,158 113,152 158,150 203,136 248,128 293,124 338,116 383,110 428,110 473,98 518,72" fill="none" stroke="#2f6fb0" stroke-width="3"/>
    <g fill="#fff" stroke="#2f6fb0" stroke-width="2"><circle cx="68" cy="158" r="4"/><circle cx="113" cy="152" r="4"/><circle cx="158" cy="150" r="4"/><circle cx="203" cy="136" r="4"/><circle cx="248" cy="128" r="4"/><circle cx="293" cy="124" r="4"/><circle cx="338" cy="116" r="4"/><circle cx="383" cy="110" r="4"/><circle cx="428" cy="110" r="4"/><circle cx="473" cy="98" r="4"/><circle cx="518" cy="72" r="4"/></g>
    <polyline points="68,158 113,170 158,186 203,172 248,166 293,166 338,160 383,160 428,196 473,180 518,168" fill="none" stroke="#b8141b" stroke-width="3"/>
    <g fill="#fff" stroke="#b8141b" stroke-width="2"><circle cx="68" cy="158" r="4"/><circle cx="113" cy="170" r="4"/><circle cx="158" cy="186" r="4"/><circle cx="203" cy="172" r="4"/><circle cx="248" cy="166" r="4"/><circle cx="293" cy="166" r="4"/><circle cx="338" cy="160" r="4"/><circle cx="383" cy="160" r="4"/><circle cx="428" cy="196" r="4"/><circle cx="473" cy="180" r="4"/><circle cx="518" cy="168" r="4"/></g>
    <g font-size="9" fill="#222">
      <rect x="524" y="50" width="46" height="28" rx="6" fill="#fff" stroke="#999"/><text x="530" y="62">183.0%</text><text x="530" y="73">Gain</text>
      <rect x="524" y="176" width="46" height="28" rx="6" fill="#fff" stroke="#999"/><text x="530" y="188">-7.4%</text><text x="530" y="199">Loss</text>
    </g>
    <line x1="120" y1="318" x2="140" y2="318" stroke="#b8141b" stroke-width="3"/>
    <text x="146" y="322" font-size="10" fill="#333">Annual Change in Market Index</text>
    <line x1="320" y1="318" x2="340" y2="318" stroke="#2f6fb0" stroke-width="3"/>
    <text x="346" y="322" font-size="10" fill="#333">Annual Change with Floor and Cap</text>
  </svg>
</div>

<h2 class="section-title" style="top:2030px">Our Blogs</h2>

<article class="blog abs" style="left:68px">
  <div class="blog-photo" role="img" aria-label="Vineyard rows at sunset" style="background:linear-gradient(180deg,#d49a55 0%,#a8773f 45%,#5a5a2a 75%,#3b3f22 100%)"></div>
  <div class="blog-meta"><span>▦ Mar 21 , 2019</span><span>◯ 20 &nbsp;♡ 12</span></div>
  <h4>What is Lorem Ipsum?</h4>
  <p>Lorem Ipsum is simply dummy the printing and typesetting industry. Lorem Ipsum has been the in the standard dummy.</p>
  <span class="more">Continue..</span>
</article>
<article class="blog abs" style="left:431px">
  <div class="blog-photo" role="img" aria-label="Hands working on a laptop with financial papers" style="background:linear-gradient(160deg,#c9d2d8 0%,#8c9aa5 50%,#dfe3e6 100%)"></div>
  <div class="blog-meta"><span>▦ Mar 21 , 2019</span><span>◯ 20 &nbsp;♡ 12</span></div>
  <h4>What is Lorem Ipsum?</h4>
  <p>Lorem Ipsum is simply dummy the printing and typesetting industry. Lorem Ipsum has been the in the standard dummy.</p>
  <span class="more">Continue..</span>
</article>
<article class="blog abs" style="left:793px">
  <div class="blog-photo" role="img" aria-label="Hands counting banknotes" style="background:linear-gradient(160deg,#1f2a33 0%,#4d5a56 50%,#9aa08a 100%)"></div>
  <div class="blog-meta"><span>▦ Mar 21 , 2019</span><span>◯ 20 &nbsp;♡ 12</span></div>
  <h4>What is Lorem Ipsum?</h4>
  <p>Lorem Ipsum is simply dummy the printing and typesetting industry. Lorem Ipsum has been the in the standard dummy.</p>
  <span class="more">Continue..</span>
</article>
<div class="btn" style="left:523px;top:2512px;width:154px;height:38px">View More</div>

<div class="testimonial-bg abs"></div>
<h2 class="section-title" style="top:2597px">Testimonials</h2>
<article class="testimonial abs" style="left:119px">
  <div class="avatar" role="img" aria-label="Portrait of client"></div>
  <h5>Marcus</h5><div class="role">Director</div>
  <p>Lorem Ipsum is simply dummy of the printing and typesetting Lorem Ipsum industry.</p>
  <svg class="go" width="20" height="20" viewBox="0 0 20 20"><circle cx="10" cy="10" r="8" fill="none" stroke="#333" stroke-width="1.6"/><path d="M6 10h8M10 6l4 4-4 4" fill="none" stroke="#333" stroke-width="1.6"/></svg>
</article>
<article class="testimonial abs" style="left:451px">
  <div class="avatar" role="img" aria-label="Portrait of client"></div>
  <h5>Owen Halbrook</h5><div class="role">Director</div>
  <p>Lorem Ipsum is simply dummy of the printing and typesetting Lorem Ipsum industry.</p>
  <svg class="go" width="20" height="20" viewBox="0 0 20 20"><circle cx="10" cy="10" r="8" fill="none" stroke="#333" stroke-width="1.6"/><path d="M6 10h8M10 6l4 4-4 4" fill="none" stroke="#333" stroke-width="1.6"/></svg>
</article>
<article class="testimonial abs" style="left:783px">
  <div class="avatar" role="img" aria-label="Portrait of client"></div>
  <h5>Elliot Varga</h5><div class="role">Director</div>
  <p>Lorem Ipsum is simply dummy of the printing and typesetting Lorem Ipsum industry.</p>
  <svg class="go" width="20" height="20" viewBox="0 0 20 20"><circle cx="10" cy="10" r="8" fill="none" stroke="#333" stroke-width="1.6"/><path d="M6 10h8M10 6l4 4-4 4" fill="none" stroke="#333" stroke-width="1.6"/></svg>
</article>
<div class="t-dots abs"><i class="on"></i><i></i><i class="on"></i></div>

<div class="newsletter-bg abs"></div>
<h2 class="section-title" style="top:3084px;font-size:28px">Join Our Newletter</h2>
<p class="subtitle" style="top:3124px;color:#444">Sign up for Our Newsletter</p>
<div class="news-input abs">Email Here</div>
<div class="btn news-btn">Subscribe</div>

<footer class="site-footer abs">
  <div class="f-brand abs"><span class="brand-mark"></span><span class="brand-name">Pinegate Lark<br>Group</span></div>
  <p class="f-about abs">Lorem Ipsum is simply dummy text of the printing and typesetting industry. Lorem Ipsum has been the industry's standard dummy text ever since the 1500s,</p>
  <span class="f-read abs">Read More..</span>
  <div class="f-links abs">
    <span class="f-head">Quick Link</span>
    <ul><li>Home</li><li>About us</li><li>Services</li><li>Blogs</li><li>Testimonials</li><li>Contact us</li><li>Career</li></ul>
  </div>
  <div class="f-address abs">
    <span class="f-head">Address</span>
    <div class="row"><svg width="12" height="14" viewBox="0 0 12 14"><path d="M6 13S1 8 1 5a5 5 0 0 1 10 0c0 3-5 8-5 8z" fill="none" stroke="#ddd" stroke-width="1.4"/><circle cx="6" cy="5" r="1.8" fill="#ddd"/></svg><span>48 Alder Lane, Suite 210, Fairhaven, CA 90210, USA</span></div>
    <div class="row"><svg width="12" height="14" viewBox="0 0 12 14"><path d="M2 1h3l1 3-2 1.5a8 8 0 0 0 3.5 3.5L9 7l3 1v3c0 1-1 2-2 2A10 10 0 0 1 0 3c0-1 1-2 2-2z" fill="#ddd"/></svg><span>555.014.2277</span></div>
    <div class="row"><svg width="12" height="14" viewBox="0 0 12 14"><rect x="1" y="2" width="10" height="10" fill="none" stroke="#ddd" stroke-width="1.4"/><rect x="3" y="4" width="6" height="3" fill="#ddd"/></svg><span>555.014.2277</span></div>
    <div class="row"><svg width="12" height="14" viewBox="0 0 12 14"><rect x="0.5" y="3" width="11" height="8" fill="none" stroke="#ddd" stroke-width="1.4"/><path d="M1 3.5 6 8l5-4.5" fill="none" stroke="#ddd" stroke-width="1.4"/></svg><span>info@pinegatelark.com</span></div>
  </div>
  <div class="f-contact abs">
    <span class="f-head">Contact us</span>
    <div class="f-fields"><span>Name</span><span>Email</span><span>Phone</span></div>
    <div class="f-message"></div>
    <span class="f-btn">Subscribe</span>
  </div>
</footer>
<div class="bottom-bar abs">
  <p class="copy abs">CopyRight © 2019 Pinegate Lark Group. All Right Reserve</p>
  <div class="socials abs"><i></i><i></i><i></i><i></i><i></i></div>
</div>

</body>
</html>
```